VOMRA Pty Ltd Business Card

Looking for a simple yet eye-catching double-sided business card design using my company logo on one side and contact details on the other.

Target Market(s)

Government

Industry/Entity Type

Communication Systems Engineering

Contact Information for Business Card

VOMRA Pty Ltd

Requirements
Nice to have
• Would be great to have a QR code so details can be scanned into contacts

```html
<!DOCTYPE html>
<html lang="en">
<head>
<meta charset="utf-8">
<title>VOMRA Pty Ltd Business Card</title>
<link rel="stylesheet" href="https://fonts.googleapis.com/css2?family=Montserrat:wght@400;500;700&display=swap">
<style>
  :root {
    --page-bg: #d8d8d8;
    --slate-dark: #2f3a42;
    --slate-light: #47525a;
    --paper-light: #f4f4f4;
    --paper-shade: #e4e4e4;
    --ink: #2d363d;
    --ink-soft: #4a4f54;
    --ink-muted: #5a5f64;
    --stripe-grey: #5d6064;
    --logo-light: #f2efec;
  }
  * { margin: 0; padding: 0; box-sizing: border-box; }
  html, body { width: 1200px; height: 1200px; overflow: hidden; }
  body {
    background: var(--page-bg);
    font-family: "Montserrat", sans-serif;
    position: relative;
  }
  .card {
    position: absolute;
    left: 234px;
    width: 730px;
    height: 418px;
    overflow: hidden;
  }
  .card-front {
    top: 160px;
    background: linear-gradient(200deg, var(--slate-light) 0%, var(--slate-dark) 70%);
    display: flex;
    align-items: center;
    justify-content: center;
  }
  .front-wordmark {
    color: var(--logo-light);
    font-weight: 500;
    font-size: 124px;
    letter-spacing: 2px;
    line-height: 1;
    margin-top: -36px;
  }
  .card-back {
    top: 632px;
    background: linear-gradient(200deg, var(--paper-light) 0%, var(--paper-shade) 80%);
  }
  .back-wordmark {
    position: absolute;
    top: 76px;
    left: 0;
    width: 100%;
    text-align: center;
    color: var(--ink);
    font-weight: 500;
    font-size: 72px;
    letter-spacing: 1px;
    line-height: 1;
  }
  .contact-list {
    position: absolute;
    left: 63px;
    top: 225px;
    list-style: none;
    color: var(--ink-soft);
    font-size: 19px;
  }
  .contact-item {
    display: flex;
    align-items: center;
    height: 27px;
  }
  .contact-icon {
    width: 16px;
    height: 16px;
    margin-right: 9px;
    fill: var(--ink);
  }
  .address {
    position: absolute;
    left: 63px;
    top: 311px;
    color: var(--ink-soft);
    font-size: 19px;
    line-height: 26px;
    font-style: normal;
  }
  .person {
    position: absolute;
    right: 61px;
    top: 226px;
    text-align: right;
  }
  .person-name {
    color: var(--ink);
    font-weight: 700;
    font-size: 30px;
    line-height: 1.1;
  }
  .person-title {
    color: var(--ink-muted);
    font-size: 19px;
    margin-top: 6px;
  }
  .footer-band {
    position: absolute;
    left: 0;
    bottom: 0;
    width: 730px;
    height: 56px;
  }
</style>
</head>
<body>
  <section class="card card-front">
    <div class="front-wordmark">VOMRA</div>
  </section>

  <section class="card card-back">
    <div class="back-wordmark">VOMRA</div>

    <ul class="contact-list">
      <li class="contact-item">
        <svg class="contact-icon" viewBox="0 0 24 24" aria-hidden="true"><path d="M6.6 10.8a15.1 15.1 0 0 0 6.6 6.6l2.2-2.2c.3-.3.7-.4 1-.2 1.1.4 2.3.6 3.6.6.6 0 1 .4 1 1V20c0 .6-.4 1-1 1A17 17 0 0 1 3 4c0-.6.4-1 1-1h3.5c.6 0 1 .4 1 1 0 1.3.2 2.5.6 3.6.1.3 0 .7-.2 1z"/></svg>
        <span>(402)-555-0147</span>
      </li>
      <li class="contact-item">
        <svg class="contact-icon" viewBox="0 0 24 24" aria-hidden="true"><path d="M2 5h20v14H2z M3 6l9 7 9-7" fill="var(--ink)"/><path d="M3 6.5l9 6.5 9-6.5" fill="none" stroke="var(--paper-light)" stroke-width="1.6"/></svg>
        <span>admin@vomra.com.au</span>
      </li>
      <li class="contact-item">
        <svg class="contact-icon" viewBox="0 0 24 24" aria-hidden="true"><circle cx="12" cy="12" r="9.5" fill="none" stroke="var(--ink)" stroke-width="2"/><ellipse cx="12" cy="12" rx="4" ry="9.5" fill="none" stroke="var(--ink)" stroke-width="2"/><path d="M2.5 12h19" stroke="var(--ink)" stroke-width="2"/></svg>
        <span>www.vomra.com.au</span>
      </li>
    </ul>

    <address class="address">
      27-29 Harlow Lane Redfield<br>
      NSW 2099 Australia
    </address>

    <div class="person">
      <div class="person-name">Marcus Ellery</div>
      <div class="person-title">Founder &amp; Director</div>
    </div>

    <svg class="footer-band" viewBox="0 362 730 56" aria-hidden="true">
      <rect x="0" y="383" width="460" height="16" fill="var(--stripe-grey)"/>
      <path d="M0 398 L440 398 C470 398 475 362 505 362 L730 362 L730 418 L0 418 Z" fill="var(--slate-dark)"/>
    </svg>
  </section>
</body>
</html>
```